Wine Label Logo NEW name too

We would like to see this done in more colors but, lighter ones too. the dark colors don't show up that well. Can you also do some on white wine and not just red wine?

Also, we aren't sure we will use the name Plumvale and wonder if you could use the name Honeyfrost with the same design to see how that looks, as well?

new wine label for a brand called Plumvale (one word) and is targeted to go after 21-40 year olds. Probably more women than men. There will be Plumvale Red, Plumvale White, Plumvale Cabernet, etc. the profile of the wine will be sweet...duh!!

would love you to come up with some TAG LINE ideas, as well. Size should be between 2 1/2 to 3 inches wide and 5 to 6 inches long. Needs place holders for varietal, Cabernet. 13.5% alcohol, area wil be California. I suggest you look at a bunch of wine labels to better understand this brief.

The final design should communicate fun, sweet, wine, young, hip

Wine labels matter. Period. Now, attempting to define “fun and contemporary” is nigh on impossible, but I think it would be safe to assume that this could mean “non-traditional.” Let’s face it. Design matters to millennial consumers. Quill, Tern Lodges, Loftly Journal – these brands are not ONLY for millennials by any means (well, maybe Tern), but design is top priority for these brands, and these brands have top priority for millennials. Feel free to do the math. If we spend money on something, we expect it to be beautiful and often times we expect social purchases like wine to act as a public reflection of our tastes and personality. This latter expectation is no different than any other generation (if arguably more intense due to our intrinsic personal branding tendencies); however, our personalities and what we are reflecting out to our peers IS different.
Updates

What about a label that is 2 1/2 to 3 inches wide and 5-6 inches long and looks like a white or off white piece of paper that has had berries poured across it with some stains and the name Plumvale Cabernet as the logo on the label?  Needs space for the AVA area grown to say California and the vintage 2011 and alcohol level in small letters 12.3%. 

Look at some wine labels to get a unique idea. Needs to appeal to 21-40 year old women. Needs to denote the wine is sweet

Reason: two partners are out of the country and I want them involved in the choice

Target Market(s)

Industry/Entity Type

Social

Logo Text

Plumvale Cabernet

Logo styles of interest
Pictorial/Combination Logo
Abstract Logo
Wordmark Logo

```html
<!DOCTYPE html>
<html lang="en">
<head>
<meta charset="utf-8">
<title>Plumvale &amp; Honeyfrost – Wine Labels</title>
<link rel="stylesheet" href="https://fonts.googleapis.com/css2?family=Parisienne&family=Sorts+Mill+Goudy:ital@0;1&family=UnifrakturMaguntia&display=swap">
<style>
  :root {
    --page-bg: #ffffff;
    --wine-red: #c21d2d;
    --wine-red-deep: #961320;
    --maroon-border: #5a0c14;
    --gold: #d9a73a;
    --gold-light: #f3d27a;
    --label-text: #ffffff;
    --label-ink: #2a0a0d;
    --sweet-pink: #fbe3e6;
    --script: "Parisienne", cursive;
    --serif: "Sorts Mill Goudy", Georgia, serif;
    --blackletter: "UnifrakturMaguntia", serif;
  }
  * { box-sizing: border-box; margin: 0; padding: 0; }
  html, body { width: 1200px; height: 900px; overflow: hidden; background: var(--page-bg); }
  .canvas { position: relative; width: 1200px; height: 900px; }

  .label { position: absolute; overflow: visible; }
  .label__shape { position: absolute; left: 0; top: 0; }
  .label__text { position: absolute; white-space: nowrap; color: var(--label-text); line-height: 1; overflow: visible; }

  /* Plumvale label */
  .label--plumvale { left: 28px; top: 28px; width: 304px; height: 430px; }
  .plumvale__crest { left: 134px; top: 30px; }
  .plumvale__varietal { left: 190px; width: 100px; top: 112px; font-family: var(--serif); font-style: italic; font-size: 22px; }
  .plumvale__name { left: 0; width: 304px; text-align: center; top: 132px; font-family: var(--script); font-size: 60px; line-height: 1.2; }
  .plumvale__tagline { left: 0; width: 304px; text-align: center; top: 212px; font-family: var(--serif); font-size: 22px; color: var(--label-ink); }
  .plumvale__sweet { left: 0; width: 304px; text-align: center; top: 248px; font-family: var(--serif); font-style: italic; font-weight: 700; font-size: 30px; color: var(--sweet-pink); }
  .plumvale__details { left: 0; width: 304px; text-align: center; top: 296px; font-family: var(--serif); font-size: 19px; line-height: 23px; }
  .plumvale__details small { display: block; font-size: 11px; line-height: 14px; }

  /* Honeyfrost label */
  .label--honeyfrost { left: 338px; top: 408px; width: 366px; height: 482px; }
  .honeyfrost__crest { left: 163px; top: 100px; }
  .honeyfrost__name { left: 0; width: 366px; text-align: center; top: 150px; font-family: var(--script); font-size: 58px; line-height: 1.2; }
  .honeyfrost__tagline { left: 62px; width: 200px; top: 222px; font-family: var(--serif); font-size: 18px; }
  .honeyfrost__sweet { left: 0; width: 366px; text-align: center; top: 264px; font-family: var(--blackletter); font-size: 24px; }
  .honeyfrost__details {
    left: 110px; top: 298px; width: 130px; padding: 6px 0 4px;
    border: 2px solid var(--gold); border-radius: 6px;
    text-align: center; font-family: var(--serif); font-size: 18px; line-height: 23px;
  }
  .honeyfrost__details small { display: block; font-size: 11px; line-height: 13px; }
</style>
</head>
<body>
<main class="canvas">

  <section class="label label--plumvale" aria-label="Plumvale Cabernet label">
    <svg class="label__shape" width="304" height="430" viewBox="0 0 304 430">
      <defs>
        <radialGradient id="plumvale-fill" cx="50%" cy="45%" r="65%">
          <stop offset="0" stop-color="var(--wine-red)"/>
          <stop offset="1" stop-color="var(--wine-red-deep)"/>
        </radialGradient>
      </defs>
      <path d="M8,12 Q152,0 296,12 C300,90 262,150 262,215 C262,290 302,340 298,416 Q152,432 8,416 C4,340 44,290 44,215 C44,150 6,90 8,12 Z" fill="url(#plumvale-fill)"/>
      <path d="M8,12 Q152,0 296,12 C300,90 262,150 262,215 C262,290 302,340 298,416 Q152,432 8,416 C4,340 44,290 44,215 C44,150 6,90 8,12 Z" fill="none" stroke="#f2b3ba" stroke-opacity="0.6" stroke-width="1.5" transform="translate(9,9) scale(0.94,0.956)"/>
    </svg>
    <svg class="label__text plumvale__crest" width="36" height="36" role="img" aria-label="crown crest emblem">
      <circle cx="18" cy="18" r="16" fill="#8e1220"/>
    </svg>
    <span class="label__text plumvale__varietal">Cabernet</span>
    <span class="label__text plumvale__name">Plumvale</span>
    <span class="label__text plumvale__tagline">good mood wine</span>
    <span class="label__text plumvale__sweet">sweet</span>
    <p class="label__text plumvale__details">Red Blend<br>California<br>Paso Robles<br>Vintange 2011<small>alc. 12.3%</small></p>
  </section>

  <section class="label label--honeyfrost" aria-label="Honeyfrost label">
    <svg class="label__shape" width="366" height="482" viewBox="0 0 366 482">
      <defs>
        <linearGradient id="honeyfrost-gold" x1="0" y1="0" x2="1" y2="1">
          <stop offset="0" stop-color="var(--gold-light)"/>
          <stop offset="0.5" stop-color="var(--gold)"/>
          <stop offset="1" stop-color="var(--gold-light)"/>
        </linearGradient>
        <radialGradient id="honeyfrost-fill" cx="50%" cy="45%" r="65%">
          <stop offset="0" stop-color="var(--wine-red)"/>
          <stop offset="1" stop-color="var(--wine-red-deep)"/>
        </radialGradient>
        <radialGradient id="honeyfrost-ornament" cx="50%" cy="50%" r="50%">
          <stop offset="0" stop-color="var(--gold)" stop-opacity="0.75"/>
          <stop offset="1" stop-color="var(--gold)" stop-opacity="0"/>
        </radialGradient>
      </defs>
      <path d="M4,4 Q183,16 362,4 C356,90 322,140 322,200 C322,270 366,320 362,478 L4,478 C0,320 44,270 44,200 C44,140 10,90 4,4 Z" fill="var(--maroon-border)"/>
      <path d="M16,16 Q183,26 350,16 C344,94 310,142 310,200 C310,272 352,322 350,466 L16,466 C14,322 56,272 56,200 C56,142 22,94 16,16 Z" fill="url(#honeyfrost-gold)"/>
      <path d="M28,28 Q183,36 338,28 C332,98 298,146 298,200 C298,274 340,326 338,454 L28,454 C26,326 68,274 68,200 C68,146 34,98 28,28 Z" fill="url(#honeyfrost-fill)"/>
      <g role="img" aria-label="gold flourish ornaments">
        <ellipse cx="80" cy="70" rx="70" ry="50" fill="url(#honeyfrost-ornament)"/>
        <ellipse cx="286" cy="70" rx="70" ry="50" fill="url(#honeyfrost-ornament)"/>
        <ellipse cx="80" cy="390" rx="80" ry="80" fill="url(#honeyfrost-ornament)"/>
        <ellipse cx="290" cy="390" rx="80" ry="80" fill="url(#honeyfrost-ornament)"/>
      </g>
    </svg>
    <svg class="label__text honeyfrost__crest" width="40" height="40" role="img" aria-label="crown crest emblem">
      <circle cx="20" cy="20" r="18" fill="#8e1220"/>
    </svg>
    <span class="label__text honeyfrost__name">Honeyfrost</span>
    <span class="label__text honeyfrost__tagline">good mood maker</span>
    <span class="label__text honeyfrost__sweet">sweet</span>
    <p class="label__text honeyfrost__details">Red Blend<br>California<br>Paso Robles<br>Vintange 2011<small>alc. 12.3%</small></p>
  </section>

</main>
</body>
</html>
```